Marlowe Group needs a business card

I would like the card to be simple but modern and elegant.
I like black and white.
or black and gold.
we are a private finance lender and also are involved in property and property developments.

please look at the business card photos i provided i would like M.G only one one side and all the other details on the other side use fonts that tie in with my theme.

Industry/Entity Type

Finance

Contact Information for Business Card

Marlowe Group (M.G) Daniel Marlowe M: 0413586207 E: danmarl@inboxmail.test

Font styles to use
Other font styles liked:
• Use fonts that would reflect our business

Colors
000000
ffffff

Requirements
Must have
• one side of details
• other side has either M.G or Marlowe Group like in the photos provided

```html
<!DOCTYPE html>
<html lang="en">
<head>
<meta charset="utf-8">
<title>Marlowe Group — Business Card</title>
<link rel="stylesheet" href="https://fonts.googleapis.com/css2?family=Cinzel:wght@400;700&family=Lato:wght@400&display=swap">
<style>
  :root {
    --stage: #6d6d6d;
    --card-black: #000000;
    --gold: #f3c623;
    --gold-soft: rgba(243, 198, 35, 0.55);
    --white: #ffffff;
    --card-yellow: #fbcd3f;
    --ink: #000000;
  }
  * { margin: 0; padding: 0; box-sizing: border-box; }
  html, body {
    width: 1200px;
    height: 900px;
    overflow: hidden;
    background: var(--stage);
  }
  .stage {
    position: relative;
    width: 1200px;
    height: 900px;
  }
  .card {
    position: absolute;
    top: 271px;
    width: 457px;
    height: 281px;
    border-radius: 14px;
    box-shadow: 2px 4px 6px rgba(0, 0, 0, 0.35);
    overflow: hidden;
  }
  .card--front {
    left: 137px;
    background: var(--card-black);
    text-align: center;
  }
  .card--back {
    left: 627px;
    background: var(--card-yellow);
  }
  .brand-mark {
    position: absolute;
    left: 0;
    right: 0;
    top: 36px;
    font-family: "Cinzel", serif;
    font-weight: 400;
    font-size: 60px;
    line-height: 1;
    color: var(--gold);
    letter-spacing: 2px;
  }
  .company-name {
    position: absolute;
    left: 0;
    right: 0;
    top: 133px;
    font-family: "Cinzel", serif;
    font-weight: 400;
    font-size: 16px;
    color: var(--gold);
    letter-spacing: 0.3px;
  }
  .person-name {
    position: absolute;
    left: 0;
    right: 0;
    top: 184px;
    font-family: "Cinzel", serif;
    font-weight: 700;
    font-size: 14.5px;
    color: var(--gold);
    letter-spacing: 0.6px;
  }
  .name-rule {
    position: absolute;
    left: 160px;
    width: 137px;
    top: 211px;
    height: 1px;
    background: linear-gradient(90deg, transparent, var(--gold-soft), transparent);
  }
  .contact-line {
    position: absolute;
    left: 0;
    right: 0;
    top: 220px;
    font-family: "Lato", sans-serif;
    font-size: 13px;
    color: var(--white);
  }
  .contact-label { color: var(--gold); }
  .contact-sep { margin: 0 4px 0 8px; }
  .back-texture {
    position: absolute;
    inset: 0;
    background: var(--card-yellow);
  }
  .back-mark {
    position: absolute;
    left: 0;
    right: 0;
    top: 96px;
    text-align: center;
    font-family: "Cinzel", serif;
    font-weight: 400;
    font-size: 84px;
    line-height: 1;
    color: var(--ink);
    letter-spacing: 3px;
  }
</style>
</head>
<body>
  <main class="stage">
    <section class="card card--front" aria-label="Card front">
      <div class="brand-mark">M.G</div>
      <p class="company-name">Marlowe Group</p>
      <p class="person-name">DANIEL MARLOWE</p>
      <div class="name-rule"></div>
      <p class="contact-line">
        <span class="contact-label">M:</span> 0413586207
        <span class="contact-sep">|</span><span class="contact-label">E:</span> danmarl@inboxmail.test
      </p>
    </section>

    <section class="card card--back" aria-label="Card back">
      <div class="back-texture" role="img" aria-label="Subtle repeating brand texture across the yellow card back"></div>
      <div class="back-mark">M.G</div>
    </section>
  </main>
</body>
</html>
```